A Hong Kong Veterinary Clinic needs a design for clinic door front signage

We are a veterinary clinic locates in the area of "San Po Kong" in Hong Kong, need a new sign (the wooden section in the photos shown below) above the front glass doors. The old signs are shown on https://www.dorwin-vet.com
Mainly the new sign should display the clinic Chinese and English names, logo, and the phone number. Able to manipulate Chinese characters is a plus.

```html
<!DOCTYPE html>
<html lang="zh-Hant">
<head>
<meta charset="utf-8">
<title>Lok Wah Animal Hospital – Shopfront Sign</title>
<link href="https://fonts.googleapis.com/css2?family=Noto+Sans+TC:wght@500;700&display=swap" rel="stylesheet">
<style>
  :root {
    --page: #e9e9e7;
    --sign-white: #ffffff;
    --ink: #1b1b1b;
    --accent: #c8161d;
    --band: #1e1c1d;
    --band-text: #ffffff;
    --photo-fur: #9a6a3c;
    --photo-grass: #6f7a4a;
    --photo-light: #e8e2da;
  }
  html, body {
    margin: 0;
    width: 1200px;
    height: 900px;
    overflow: hidden;
    background: var(--page);
  }
  .canvas {
    position: relative;
    width: 1200px;
    height: 900px;
  }
  .sign {
    position: absolute;
    left: 20px;
    top: 262px;
    width: 1160px;
    height: 376px;
    background: var(--sign-white);
    overflow: hidden;
    box-shadow: 0 2px 10px rgba(0,0,0,0.15);
    font-family: "Noto Sans TC", sans-serif;
  }
  .sign-art {
    position: absolute;
    inset: 0;
  }
  .brand-mark {
    position: absolute;
    left: 330px;
    top: 44px;
    display: flex;
    align-items: center;
    gap: 10px;
    font-weight: 500;
    font-size: 22px;
    line-height: 1;
    color: var(--ink);
  }
  .brand-mark .dot {
    width: 30px;
    height: 30px;
    border-radius: 50%;
    background: var(--accent);
  }
  .name-zh {
    position: absolute;
    left: 520px;
    top: 14px;
    margin: 0;
    font-weight: 500;
    font-size: 80px;
    letter-spacing: 2px;
    color: var(--ink);
    line-height: 1;
  }
  .name-en {
    position: absolute;
    right: 40px;
    top: 112px;
    margin: 0;
    text-align: right;
    font-weight: 500;
    color: var(--ink);
    line-height: 1;
  }
  .name-en .place,
  .name-en .kind {
    display: block;
    font-size: 48px;
  }
  .name-en .kind {
    margin-top: 10px;
  }
  .phone {
    position: absolute;
    right: 40px;
    top: 242px;
    margin: 0;
    font-weight: 700;
    font-size: 76px;
    color: var(--band-text);
    line-height: 1;
    letter-spacing: 2px;
  }
</style>
</head>
<body>
<main class="canvas">
  <section class="sign" aria-label="Shopfront sign">
    <svg class="sign-art" viewBox="0 0 1160 376" width="1160" height="376" preserveAspectRatio="none">
      <defs>
        <linearGradient id="photoTone" x1="0" y1="0" x2="1" y2="1">
          <stop offset="0" stop-color="var(--photo-grass)"/>
          <stop offset="0.35" stop-color="var(--photo-fur)"/>
          <stop offset="0.6" stop-color="var(--photo-light)"/>
          <stop offset="1" stop-color="var(--photo-grass)"/>
        </linearGradient>
      </defs>
      <rect class="info-band" x="560" y="232" width="600" height="104" fill="var(--band)"/>
      <path class="photo-area" role="img" aria-label="Photo of a smiling long-haired dog on a grass lawn"
            d="M0 0 H280 C250 150 380 260 520 376 H0 Z"
            fill="url(#photoTone)"/>
    </svg>

    <div class="brand-mark"><span class="dot"></span>Lok Wah</div>

    <h1 class="name-zh">樂華動物醫院</h1>
    <p class="name-en">
      <span class="place">Lok Wah</span>
      <span class="kind">Animal Hospital</span>
    </p>
    <p class="phone">2388 5170</p>
  </section>
</main>
</body>
</html>
```